Home Staging Company needs business card design

We're a home staging company called Brightly Settled Home Staging. We would like a business card design that includes aqua and gray. Our current logo of house within chair is fine but I find we almost always use the logo in one color. I'll upload images of front and back of our current card and our logo. Note that we have dropped "Solutions" from our company name and don't want to include it on the card.

Target Market(s)

Realtors and homeowners - people interested in selling their homes

Contact Information for Business Card

Marisol Thistlewood
Brightly Settled Home Staging
757-555-0193
www.brightlysettled.com
marisol@brightlysettled.com

Font styles to use
Serif
Script

Requirements
Must have
• My logo and contact details
• UPDATE***
• I forgot to say that the company name should be included on the front of the card somehow.

```html
<!DOCTYPE html>
<html lang="en">
<head>
<meta charset="utf-8">
<title>Brightly Settled Home Staging – Business Card</title>
<link rel="stylesheet" href="https://fonts.googleapis.com/css2?family=Playfair+Display:wght@500&family=Questrial&display=swap">
<style>
  :root {
    --backdrop: #3a3a3a;
    --card: #1c1c1d;
    --card-edge: #141414;
    --gloss: #3b3b3d;
    --aqua: #4fb8c9;
    --white: #f2f2f2;
    --muted: #c9c9c9;
  }
  * { margin: 0; padding: 0; box-sizing: border-box; }
  html, body { width: 799px; height: 1200px; overflow: hidden; }
  body {
    background: var(--backdrop);
    position: relative;
    font-family: "Questrial", sans-serif;
  }
  .card {
    position: absolute;
    left: 80px;
    width: 640px;
    height: 366px;
    background: var(--card);
    border: 1px solid var(--card-edge);
    box-shadow: 0 14px 30px rgba(0,0,0,0.45);
  }
  .card--front { top: 140px; }
  .card--back { top: 700px; }

  .front-mark {
    position: absolute;
    inset: 0;
    display: flex;
    align-items: center;
    justify-content: center;
    gap: 18px;
  }
  .front-mark__dot {
    width: 64px; height: 64px;
    border-radius: 50%;
    background: var(--gloss);
  }
  .front-mark__name {
    font-family: "Playfair Display", serif;
    font-weight: 500;
    font-size: 30px;
    color: var(--gloss);
    line-height: 1.15;
  }

  .brand {
    position: absolute;
    left: 34px; top: 32px;
    display: flex;
    align-items: center;
    gap: 14px;
  }
  .brand__dot {
    width: 58px; height: 58px;
    border-radius: 50%;
    background: var(--aqua);
  }
  .brand__name {
    font-family: "Playfair Display", serif;
    font-weight: 500;
    font-size: 22px;
    color: var(--white);
    line-height: 1.15;
  }

  .person {
    position: absolute;
    left: 34px; top: 138px;
  }
  .person__name {
    font-size: 25px;
    color: var(--white);
  }
  .person__surname { color: var(--aqua); }
  .person__title {
    font-size: 14px;
    color: var(--muted);
    margin-top: 4px;
  }

  .contacts {
    position: absolute;
    left: 34px; top: 236px;
    list-style: none;
  }
  .contacts__item {
    display: flex;
    align-items: center;
    gap: 12px;
    font-size: 16px;
    color: var(--white);
    height: 28px;
  }
  .contacts__icon { width: 16px; height: 16px; fill: var(--aqua); flex: none; }
</style>
</head>
<body>
  <section class="card card--front">
    <div class="front-mark">
      <span class="front-mark__dot"></span>
      <span class="front-mark__name">Brightly Settled<br>Home Staging</span>
    </div>
  </section>

  <section class="card card--back">
    <div class="brand">
      <span class="brand__dot"></span>
      <span class="brand__name">Brightly Settled<br>Home Staging</span>
    </div>

    <div class="person">
      <p class="person__name">Marisol <span class="person__surname">Thistlewood</span></p>
      <p class="person__title">Managing Director</p>
    </div>

    <ul class="contacts">
      <li class="contacts__item">
        <svg class="contacts__icon" viewBox="0 0 16 16" aria-hidden="true"><path d="M3 1h3l1.5 4-2 1.5a9 9 0 0 0 4 4L11 8.5l4 1.5v3a2 2 0 0 1-2 2A12 12 0 0 1 1 3a2 2 0 0 1 2-2z"/></svg>
        757-555-0193
      </li>
      <li class="contacts__item">
        <svg class="contacts__icon" viewBox="0 0 16 16" aria-hidden="true"><path d="M8 1a7 7 0 1 0 0 14A7 7 0 0 0 8 1zm0 1.5c.8.8 1.5 2.3 1.7 4.5H6.3C6.5 4.8 7.2 3.3 8 2.5zM5 7H2.6A5.5 5.5 0 0 1 6 2.8 9 9 0 0 0 5 7zm0 2a9 9 0 0 0 1 4.2A5.5 5.5 0 0 1 2.6 9zm1.3 0h3.4c-.2 2.2-.9 3.7-1.7 4.5-.8-.8-1.5-2.3-1.7-4.5zM11 9h2.4A5.5 5.5 0 0 1 10 13.2 9 9 0 0 0 11 9zm0-2a9 9 0 0 0-1-4.2A5.5 5.5 0 0 1 13.4 7z"/></svg>
        www.brightlysettled.com
      </li>
      <li class="contacts__item">
        <svg class="contacts__icon" viewBox="0 0 16 16" aria-hidden="true"><path d="M1 3h14v10H1zm1.5 1.5v.3L8 9l5.5-4.2v-.3zm0 2.2v4.8h11V6.7L8 11z"/></svg>
        marisol@brightlysettled.com
      </li>
    </ul>
  </section>
</body>
</html>
```